Helen's 40th Invitation

I need an invitation designed for a 40th birthday in Singapore. The theme is a "long lunch", set in a colonial garden (black and white house - Singapore style if you want to Google or Bing it).
Look and feel should be simple, elegant, stylish, bold, fresh, minimalist. Nothing fussy, intricate, formal or too colourful. No intials, not wedding-like, minimal colour (no golds).
Setting will be garden setting with champagne, white marquee, white table cloths, long trestle tables, fresh white floowers (lilys or hydrangas).
Format should be PC friendly (jpeg, gif, pdf etc).
Size is flexible to accomodate design - it will be emailed as an attachment.
Details to include:
- Saturday, 27th November, 2010
Time - From 1pm.
Address - 214 Fernbrook Rise, Singapore
Dress: Garden Glam
RSVP - jolwen@quarlixmail.com by 13 November, 2010

```html
<!DOCTYPE html>
<html lang="en">
<head>
<meta charset="utf-8">
<title>Long Lunch – Helen's 40th</title>
<link rel="stylesheet" href="https://fonts.googleapis.com/css2?family=Bodoni+Moda:wght@400&family=Poppins:wght@500&family=Roboto+Condensed:wght@400;700&display=swap">
<style>
  :root {
    --page: #ffffff;
    --card-brown: #3d2314;
    --ink-white: #ffffff;
    --vine-green: #2f8a5a;
  }
  html, body {
    margin: 0;
    padding: 0;
    width: 1200px;
    height: 900px;
    overflow: hidden;
    background: var(--page);
  }
  .invitation {
    position: absolute;
    left: 96px;
    top: 186px;
    width: 1000px;
    height: 504px;
    background: var(--card-brown);
    overflow: hidden;
    color: var(--ink-white);
  }
  .vine-decoration {
    position: absolute;
    left: 0;
    top: 40px;
    width: 1000px;
    height: 120px;
    background: linear-gradient(180deg,
      rgba(47,138,90,0) 0%,
      rgba(47,138,90,0.55) 50%,
      rgba(47,138,90,0) 100%);
  }
  .event-title {
    position: absolute;
    left: 24px;
    top: 10px;
    width: 952px;
    height: 170px;
  }
  .event-title text {
    font-family: "Bodoni Moda", "Didot", serif;
    font-weight: 400;
    font-size: 212px;
    fill: var(--ink-white);
  }
  .occasion {
    position: absolute;
    right: 18px;
    top: 176px;
    margin: 0;
    font-family: "Poppins", "Century Gothic", sans-serif;
    font-weight: 500;
    font-size: 40px;
    line-height: 1.1;
  }
  .details {
    position: absolute;
    left: 26px;
    right: 18px;
    top: 0;
    bottom: 0;
    font-family: "Roboto Condensed", "Helvetica Neue", sans-serif;
    font-size: 25px;
    line-height: 1;
  }
  .details p {
    position: absolute;
    margin: 0;
    white-space: nowrap;
  }
  .details strong { font-weight: 700; }
  .detail-date { left: 0; top: 350px; }
  .detail-venue { left: 0; top: 400px; }
  .detail-dress { left: 0; top: 457px; }
  .detail-rsvp { right: 0; top: 457px; }
</style>
</head>
<body>
  <main class="invitation">
    <div class="vine-decoration" role="img" aria-label="Sweeping green garden vine with curling tendrils and leaves across the top of the card"></div>

    <svg class="event-title" viewBox="0 0 952 170" aria-label="Long Lunch">
      <text x="0" y="160" textLength="950" lengthAdjust="spacingAndGlyphs">LONG LUNCH</text>
    </svg>

    <h2 class="occasion">Helen's 40th</h2>

    <section class="details">
      <p class="detail-date">Saturday, <strong>27th Nov 2010</strong> From <strong>1pm</strong></p>
      <p class="detail-venue"><strong>VENUE</strong> 214 Fernbrook Rise, Singapore</p>
      <p class="detail-dress">Dress <strong>Garden Glam</strong></p>
      <p class="detail-rsvp"><strong>RSVP</strong> jolwen@quarlixmail.com by <strong>13th Nov 2010</strong></p>
    </section>
  </main>
</body>
</html>
```